Design my site www.brieflyledger.com

So here is what I am thinking in terms of design:

https://plenvo.com

https://www.skyluxair.com

http://kalvex.com/harbor-plaza-tower/

I want the theme to be white and blue (royal blue). I attached a paint picture of what I would like the site to look like in terms of placing the text. Generally, what I like about the sites above is that they are simple, you can navigate easily and have some kind of idea of what's going on by looking at the center (picture and motto). Let's establish a clear understanding of how the functional part of the site would look like. Please see the picture attached.

I want to keep it simple: On top would be the Name 'BRIEFLY ledger", somewhere to the right on top on the page would be 'Sign in" button.

In the center would be a picture (maybe a video) with the Motto (on top of it all in capital) OBSERVE NAVIGATE DECIDE and below would be the "sign up now"

Below the picture (like on kalvex.com site) or to the left on top of the page would be "About Us', "Press" "Contact Us' buttons.

Then once the user gets to his page his got 3 tabs " Press Headlines", "Events", " Briefings".

we would keep the same format I only have on the site, but separate for every Tab.

I do not want the user to get distracted. I also want him to be able to access the page though mobile phone and be able to get automatic updates just like Zorvan Pings without having to sign in daily.

The landing page must be minimalist yet with business/corporate feel where users can navigate easily and a "what you see is what you get" approach. You want an image or video (personally I prefer the video.. it does capture the users attention instantly, as long as it is an interesting video), with your taglines in it.

Sections available to public: About Us, Contact Us, Landing Page with Signup Option

Private: Public Sections + User Account Page, Tabs for (Events, Press Headlines, Briefings)

Target Market(s)

PR/media monitoring/diplomatic community

Coding

Coded - Design and coding required

Number of Pages Required

1 page

Font styles to use
Serif
Sans Serif

Colors
0255a3
ec1f27

Requirements
Must have
• a simple landing page, that is user friendly.
Nice to have
• a video with the explanation of how to navigate the site
Should not have
• too many colors, graphs etc.

```html
<!DOCTYPE html>
<html lang="en">
<head>
<meta charset="utf-8">
<title>BRIEFLY ledger — Newspapers Headlines</title>
<link rel="stylesheet" href="https://fonts.googleapis.com/css2?family=Jost:wght@500&family=Open+Sans:wght@400;700&display=swap">
<style>
  :root {
    --page-white: #ffffff;
    --royal-blue: #134f8f;
    --brand-blue: #0255a3;
    --brand-red: #ec1f27;
    --tab-grey: #c8c8c8;
    --tab-grey-edge: #8f8f8f;
    --ink: #1a1a1a;
    --rule: #9a9a9a;
    --city-haze-top: #ffffff;
    --city-haze-bottom: #e4e1dc;
  }
  * { box-sizing: border-box; margin: 0; padding: 0; }
  html, body { width: 1200px; height: 600px; overflow: hidden; }
  body {
    position: relative;
    font-family: "Open Sans", Arial, sans-serif;
    color: var(--ink);
    background: var(--page-white);
  }
  .city-backdrop {
    position: absolute; inset: 0;
    background: linear-gradient(180deg, var(--city-haze-top) 0%, var(--city-haze-top) 28%, #f1efeb 48%, var(--city-haze-bottom) 100%);
  }
  .brand {
    position: absolute; left: 160px; top: 0; width: 64px; height: 62px;
    display: flex; align-items: center; justify-content: center;
    font-family: "Open Sans", Arial, sans-serif; font-weight: 700;
    font-size: 10px; line-height: 1.15; text-align: center;
    color: var(--brand-blue);
  }
  .sign-up {
    position: absolute; left: 956px; top: 12px; width: 82px; height: 28px;
    border: 1.5px solid #333; border-radius: 14px; background: var(--page-white);
    font: 700 10.5px/25px "Open Sans", Arial, sans-serif; letter-spacing: .4px;
    text-align: center; color: var(--ink); text-decoration: none;
  }
  .tabs { position: absolute; top: 106px; left: 0; width: 100%; height: 80px; }
  .tab {
    position: absolute; top: 0; height: 70px;
    display: flex; align-items: center; justify-content: center;
    font: 500 19.5px "Jost", "Futura", sans-serif; letter-spacing: .3px;
    color: var(--page-white); text-transform: uppercase;
    background: var(--tab-grey); border-bottom: 2px solid var(--tab-grey-edge);
    border-radius: 2px 2px 0 0;
  }
  .tab--active { background: var(--royal-blue); border-bottom-color: #0d3a6a; }
  .tab--headlines { left: 188px; width: 338px; }
  .tab--events { left: 530px; width: 204px; }
  .tab--briefing { left: 737px; width: 276px; }
  .tab-pointer { position: absolute; left: 351px; top: 70px; }
  .column-rule { position: absolute; top: 240px; width: 1px; height: 282px; background: var(--rule); }
  .article { position: absolute; top: 239px; width: 212px; }
  .article__photo {
    width: 210px; height: 117px; border: 2px solid #d6d6d6; border-radius: 3px;
    box-shadow: 0 1px 3px rgba(0,0,0,.18);
  }
  .photo--street { background: linear-gradient(135deg, #b9a684 0%, #8c8a7c 45%, #c9c49a 100%); }
  .photo--skyline-sun { background: linear-gradient(120deg, #d8e2ea 0%, #e8c98f 45%, #5a4632 100%); }
  .photo--skyline-day { background: linear-gradient(180deg, #dfe8ef 0%, #b9c5cf 60%, #5f6670 100%); }
  .article__meta {
    margin-top: 26px; display: flex; align-items: center; font-size: 12.5px; line-height: 16px;
  }
  .article__meta .divider { width: 1.5px; height: 17px; background: var(--ink); margin: 0 13px 0 14px; }
  .article__excerpt { margin-top: 13px; font-size: 12.5px; line-height: 14.6px; width: 210px; }
  .article__link {
    display: inline-block; margin-top: 14px; margin-left: -1px; font-size: 12.5px; line-height: 16px;
    color: var(--ink); text-decoration: none; border-bottom: 1.5px solid var(--ink); padding-bottom: 1px;
  }
</style>
</head>
<body>
  <div class="city-backdrop" role="img" aria-label="Faded city skyline photograph behind the page"></div>

  <header>
    <div class="brand">BRIEFLY<br>ledger</div>
    <a class="sign-up" href="#">SIGN UP</a>
  </header>

  <nav class="tabs">
    <div class="tab tab--headlines tab--active">Newspapers Headlines</div>
    <div class="tab tab--events">Events</div>
    <div class="tab tab--briefing">Daily Briefing</div>
    <svg class="tab-pointer" width="16" height="8" viewBox="0 0 16 8" aria-hidden="true">
      <polygon points="0,0 16,0 8,8" fill="#0d3a6a"/>
    </svg>
  </nav>

  <main>
    <span class="column-rule" style="left:463px"></span>
    <span class="column-rule" style="left:742px"></span>

    <article class="article" style="left:214px">
      <div class="article__photo photo--street" role="img" aria-label="Aerial view of a busy city avenue with taxis"></div>
      <div class="article__meta"><span>Jan 05, 2016</span><span class="divider"></span><span>Source</span></div>
      <p class="article__excerpt">Duis autem vel eum iriure dolor in hendrerit in vulputate velit esse mo-lestievel illum dolore eu feugiat nulla facilisis at vero eros et accumsan et iusto odio</p>
      <a class="article__link" href="#">Read More</a>
    </article>

    <article class="article" style="left:495px">
      <div class="article__photo photo--skyline-sun" role="img" aria-label="Businessman beside city towers at sunset"></div>
      <div class="article__meta"><span>Jan 05, 2016</span><span class="divider"></span><span>Source</span></div>
      <p class="article__excerpt">Duis autem vel eum iriure dolor in hendrerit in vulputate velit esse mo-lestievel illum dolore eu feugiat nulla facilisis at vero eros et accumsan et iusto odio</p>
      <a class="article__link" href="#">Read More</a>
    </article>

    <article class="article" style="left:781px">
      <div class="article__photo photo--skyline-day" role="img" aria-label="Businessman standing on a rooftop overlooking a skyline"></div>
      <div class="article__meta"><span>Jan 05, 2016</span><span class="divider"></span><span>Source</span></div>
      <p class="article__excerpt">Duis autem vel eum iriure dolor in hendrerit in vulputate velit esse mo-lestievel illum dolore eu feugiat nulla facilisis at vero eros et accumsan et iusto odio</p>
      <a class="article__link" href="#">Read More</a>
    </article>
  </main>
</body>
</html>
```